Web design for financial services

A modern web design of financial services (brokerage firm)
Req.s and technology tags :
- Very mobile friendly.
- One paged with some inner pages.
- Animated sticky header .
- Member login area for e-trade.
- Support RTL language.
- HTML & CSS.

The logo will be Home link
• MPTR :
WHO WE ARE
Content :
i) Board of Directors
ii) Mission Statement
iii) Corporate Values
iv) Regulations
• Financial Services :
WHAT WE DO
Content:
i) Electronic trading
ii) Trading desk
iii) Institutional
iv) Investors Education
• News
• Market Tools
• Forms---- opens new page
• Careers---- opens new page
• Contact Us----opens new page

The website is :
http://www.mptr-doha-example.com/

The logo need some changes to be more modern and impressively , but with keeping same structure .

Some related websites :
https://www.lv-bourse.example/

financial market

Financial Service

Coded - Design and coding required

2 page

• same fonts of http://www.kwdholdings.example/

• - Very mobile friendly.
• - One paged with some inner pages.
• - Animated sticky header .
• - Member login area for e-trade.
• - Support RTL language.
• - HTML & CSS.
• Slider , some Qatari theme,
• i like the video inside the home page
• ex :http://www.kwdholdings.example/

```html
<!DOCTYPE html>
<html lang="en">
<head>
<meta charset="utf-8">
<title>MPTR — Financial Securities</title>
<link href="https://fonts.googleapis.com/css2?family=Mulish:wght@400;600;700;800&display=swap" rel="stylesheet">
<style>
:root{
  --red:#9c2420;
  --red-dark:#7e1a17;
  --red-light:#b53a33;
  --ink:#333333;
  --text:#5a5a5a;
  --muted:#8a8a8a;
  --line:#d8d8d8;
  --grey-bg:#efefef;
  --footer:#9b9b9b;
  --white:#ffffff;
}
*{box-sizing:border-box;margin:0;padding:0}
html,body{width:1200px;height:2862px;overflow:hidden}
body{font-family:"Mulish",Arial,sans-serif;color:var(--text);background:var(--white)}
a{color:inherit;text-decoration:none}

/* Header */
.site-header{height:114px;position:relative;background:var(--white);z-index:5}
.brand{position:absolute;left:160px;top:0;width:134px;height:134px;border-radius:50%;background:var(--white);display:flex;align-items:center;justify-content:center;box-shadow:0 2px 6px rgba(0,0,0,.08)}
.brand-name{font-weight:800;font-size:30px;color:var(--red);letter-spacing:1px}
.header-tools{position:absolute;right:154px;top:12px;display:flex;gap:8px}
.btn-login,.lang-select{height:34px;border:1px solid var(--line);font-size:14px;display:flex;align-items:center;gap:6px;padding:0 10px;white-space:nowrap}
.btn-login{border-color:var(--red);color:var(--red);width:96px;justify-content:center}
.lang-select{color:var(--muted);font-size:12px;width:96px}
.lang-dot{width:14px;height:14px;border-radius:50%;background:#c9c9d6;flex:none}
.main-nav{position:absolute;right:150px;top:62px;display:flex;gap:36px;font-size:17px;color:var(--ink);white-space:nowrap}
.main-nav a{position:relative;padding-bottom:30px}
.main-nav a.active{color:var(--red);font-weight:700}
.main-nav a.active::after{content:"";position:absolute;left:-8px;right:-8px;bottom:0;height:3px;background:var(--red)}

/* Hero */
.hero{height:525px;position:relative;overflow:hidden}
.hero-media{position:absolute;inset:0;background:linear-gradient(180deg,#1c2d5a 0%,#243e78 45%,#2d3d66 70%,#3b3a4e 100%)}
.hero-content{position:absolute;left:0;right:0;top:150px;text-align:center;color:var(--white)}
.play-button{width:102px;height:102px;margin:0 auto 22px;display:block}
.hero-title{font-size:41px;line-height:44px;font-weight:700;letter-spacing:.5px;text-transform:uppercase}

/* Who we are */
.who{height:445px;position:relative}
.who-text{position:absolute;left:151px;top:72px;width:490px}
.section-title{font-size:27px;font-weight:700;color:var(--ink);letter-spacing:.5px;margin-bottom:22px}
.body-copy{font-size:13px;line-height:21px;color:var(--text);margin-bottom:18px}
.more-link{display:inline-block;font-size:14px;font-weight:700;color:var(--red);padding-bottom:3px;border-bottom:1px solid var(--red);margin-top:6px}
.who-image{position:absolute;left:652px;top:29px}

/* What we do */
.what{height:452px;background:var(--grey-bg);position:relative}
.what-illustration{position:absolute;left:143px;top:80px;width:420px;height:267px;border-radius:6px;background:linear-gradient(135deg,#e9ecef,#dfe6ea 60%,#f3dcdb)}
.what-text{position:absolute;left:622px;top:112px;width:420px}
.what-text .section-title{color:var(--red)}

/* News */
.news{height:454px;background:linear-gradient(90deg,var(--red-light) 0%,var(--red) 50%,var(--red-dark) 100%);position:relative}
.news-title{position:absolute;left:151px;top:40px;font-size:34px;font-weight:400;color:var(--white)}
.news-track{position:absolute;left:153px;top:99px;display:flex;gap:18px}
.news-card{width:282px;height:311px;background:rgba(100,15,13,.55)}
.news-photo{height:160px;background:linear-gradient(135deg,#c8ccd2,#8e959e)}
.news-body{padding:20px 20px 0;color:var(--white)}
.news-date{font-size:12px;opacity:.9}
.news-head{font-size:17px;font-weight:400;margin:6px 0 6px}
.news-excerpt{font-size:11px;line-height:15px;opacity:.85}
.news-more{display:inline-block;margin-top:12px;font-size:12px;font-weight:700;border-bottom:1px solid var(--white);padding-bottom:2px}
.slider-arrow{position:absolute;top:225px}
.slider-arrow.prev{left:112px}
.slider-arrow.next{left:1055px}

/* Market tools */
.tools{height:481px;position:relative}
.tools-title{position:absolute;left:149px;top:70px;font-size:33px;font-weight:400;color:var(--ink)}
.tools-grid{position:absolute;left:149px;top:130px;display:flex;gap:14px}
.tool-box{width:292px;height:286px;border:1px solid var(--line);background:var(--white);padding:26px 18px 0}
.tool-head{display:flex;align-items:center;justify-content:center;gap:8px;font-size:17px;color:var(--red);font-weight:600;margin-bottom:14px;white-space:nowrap}
.tool-rule{width:28px;height:2px;background:var(--red);position:relative;flex:none}
.tool-rule::after{content:"";position:absolute;top:-2px;width:6px;height:6px;border-radius:50%;background:var(--red)}
.tool-rule.left::after{right:0}
.tool-rule.right::after{left:0}
.tool-list{list-style:none;font-size:13px;color:var(--text);text-align:center;margin:0 14px}
.tool-list li{height:27px;line-height:26px;border-bottom:1px solid #e4e4e4}

/* Footer */
.site-footer{height:391px;background:var(--footer);position:relative;color:var(--white)}
.footer-brand{position:absolute;left:151px;top:60px;width:200px;height:200px;border-radius:50%;border:4px solid var(--white);display:flex;align-items:center;justify-content:center;font-size:48px;font-weight:800}
.footer-col{position:absolute;top:60px}
.footer-col h4{font-size:21px;font-weight:400;margin-bottom:16px}
.footer-company{left:414px}
.footer-company li{list-style:none;font-size:12px;line-height:28px}
.footer-contact{left:614px}
.contact-row{display:flex;gap:12px;font-size:12px;line-height:20px;margin-bottom:8px}
.contact-row svg{flex:none;margin-top:2px}
.footer-follow{left:885px}
.social{display:flex;gap:10px}
.social span{width:34px;height:34px;border-radius:50%;background:var(--white);opacity:.9}
.footer-bottom{position:absolute;left:151px;right:151px;top:328px;border-top:1px solid #b3b3b3;text-align:center;font-size:11px;padding-top:22px}
</style>
</head>
<body>

<header class="site-header">
  <a class="brand" href="#"><span class="brand-name">MPTR</span></a>
  <div class="header-tools">
    <a class="btn-login" href="#">
      <svg width="11" height="13" viewBox="0 0 11 13"><rect x="0" y="5" width="11" height="8" fill="#9c2420"/><path d="M2.5 5V3.5a3 3 0 0 1 6 0V5" fill="none" stroke="#9c2420" stroke-width="1.6"/></svg>
      Login
    </a>
    <div class="lang-select"><span class="lang-dot"></span>English ⌄</div>
  </div>
  <nav class="main-nav">
    <a class="active" href="#">MPTR</a>
    <a href="#">Financial Service</a>
    <a href="#">News</a>
    <a href="#">Market Tool</a>
    <a href="#">Forms</a>
    <a href="#">Careers</a>
  </nav>
</header>

<section class="hero">
  <div class="hero-media" role="img" aria-label="Night skyline of a modern city with lit glass towers"></div>
  <div class="hero-content">
    <svg class="play-button" viewBox="0 0 102 102"><circle cx="51" cy="51" r="49" fill="none" stroke="#fff" stroke-width="2"/><path d="M43 35 L67 51 L43 67 Z" fill="none" stroke="#fff" stroke-width="2"/></svg>
    <h1 class="hero-title">We are Meridian Pearl<br>Trading Resources</h1>
  </div>
</section>

<section class="who">
  <div class="who-text">
    <h2 class="section-title">WHO WE ARE</h2>
    <p class="body-copy">Meridian Pearl Trading Resources is a private Qatari company that aims to provide secure and technologically advanced methods of trading to its clients. Those facilities enables clients to trade faster, more secure &amp; private. Having this strategy in our in minds, with this online portal we begin.</p>
    <p class="body-copy">Praesent elementum elit at tellus nec ultricies sit amet porttitor mattis enim In massa libero interdum nec interdum vel blandit sed nulla In</p>
    <a class="more-link" href="#">About MPTR ›</a>
  </div>
  <svg class="who-image" width="422" height="362" viewBox="0 0 422 362" role="img" aria-label="Boardroom overlooking a city at night with market charts">
    <defs><linearGradient id="whoFill" x1="0" y1="0" x2="0" y2="1"><stop offset="0" stop-color="#1e3f7a"/><stop offset=".55" stop-color="#2b62a8"/><stop offset="1" stop-color="#15284d"/></linearGradient></defs>
    <polygon points="0,181 95,0 327,0 422,181 327,362 95,362" fill="url(#whoFill)"/>
  </svg>
</section>

<section class="what">
  <div class="what-illustration" role="img" aria-label="Flat line illustration of a briefcase surrounded by finance icons"></div>
  <div class="what-text">
    <h2 class="section-title">WHAT WE DO</h2>
    <p class="body-copy">Integer congue augue et malesuada iaculis ipsum dui aliquet felis at cursus magna nisl nec elit Praesent elementum elit at tellus nec ultricies sit amet porttitor mattis enim In massa</p>
    <p class="body-copy">Libero interdum nec interdum vel blandit sed nulla In ullamcorper est eget tempor cursus neque mi consectetuer mi</p>
    <a class="more-link" href="#">Read More ›</a>
  </div>
</section>

<section class="news">
  <h2 class="news-title">News</h2>
  <svg class="slider-arrow prev" width="24" height="50" viewBox="0 0 24 50"><path d="M22 2 L2 25 L22 48" fill="none" stroke="#fff" stroke-width="1.5"/></svg>
  <div class="news-track">
    <article class="news-card">
      <div class="news-photo" role="img" aria-label="Open-plan office with staff at desks"></div>
      <div class="news-body">
        <p class="news-date">25 Jan 2016</p>
        <h3 class="news-head">News Tittle here</h3>
        <p class="news-excerpt">Praesent elementum elit at tellus nec ultricies sit amet porttitor mattis enim In massa</p>
        <a class="news-more" href="#">READ MORE</a>
      </div>
    </article>
    <article class="news-card">
      <div class="news-photo" role="img" aria-label="Desk with laptop, calculator and paperwork"></div>
      <div class="news-body">
        <p class="news-date">25 Jan 2016</p>
        <h3 class="news-head">News Tittle here</h3>
        <p class="news-excerpt">Praesent elementum elit at tellus nec ultricies sit amet porttitor mattis enim In massa</p>
        <a class="news-more" href="#">READ MORE</a>
      </div>
    </article>
    <article class="news-card">
      <div class="news-photo" role="img" aria-label="Hands reviewing financial charts on a table"></div>
      <div class="news-body">
        <p class="news-date">25 Jan 2016</p>
        <h3 class="news-head">News Tittle here</h3>
        <p class="news-excerpt">Praesent elementum elit at tellus nec ultricies sit amet porttitor mattis enim In massa</p>
        <a class="news-more" href="#">READ MORE</a>
      </div>
    </article>
  </div>
  <svg class="slider-arrow next" width="24" height="50" viewBox="0 0 24 50"><path d="M2 2 L22 25 L2 48" fill="none" stroke="#fff" stroke-width="1.5"/></svg>
</section>

<section class="tools">
  <h2 class="tools-title">Market Tools</h2>
  <div class="tools-grid">
    <div class="tool-box">
      <h3 class="tool-head"><span class="tool-rule left"></span>Most Active Company<span class="tool-rule right"></span></h3>
      <ul class="tool-list">
        <li>Praesent elementum</li><li>Elit at tellus nec</li><li>Ultricies sit</li><li>Amet porttitor</li><li>Mattis enim In</li><li>Massa libero interdum</li><li>Nec interdum</li>
      </ul>
    </div>
    <div class="tool-box">
      <h3 class="tool-head"><span class="tool-rule left"></span>Top Gainer<span class="tool-rule right"></span></h3>
      <ul class="tool-list">
        <li>Donec dictum</li><li>Lectus non odio</li><li>Cras a ante vitae</li><li>Enim iaculis aliquam</li><li>Mauris nunc quam</li><li>Penenatis nec</li><li>Euismod sit amet</li>
      </ul>
    </div>
    <div class="tool-box">
      <h3 class="tool-head"><span class="tool-rule left"></span>Top Losers<span class="tool-rule right"></span></h3>
      <ul class="tool-list">
        <li>Libero interdum</li><li>Praesent elementum</li><li>Elit at tellus nec</li><li>Ultricies sit</li><li>Amet porttitor</li><li>Mattis enim In</li>
      </ul>
    </div>
  </div>
</section>

<footer class="site-footer">
  <div class="footer-brand">MPTR</div>
  <div class="footer-col footer-company">
    <h4>Company</h4>
    <ul><li>MPTR</li><li>Financial Service</li><li>News</li><li>Market Tool</li><li>Forms</li><li>Careers</li></ul>
  </div>
  <div class="footer-col footer-contact">
    <h4>Contact Us</h4>
    <div class="contact-row"><svg width="14" height="18" viewBox="0 0 14 18"><path d="M7 0a7 7 0 0 0-7 7c0 5 7 11 7 11s7-6 7-11a7 7 0 0 0-7-7z" fill="#fff"/><circle cx="7" cy="7" r="2.5" fill="#9b9b9b"/></svg><span>214 Corniche Tower Suite B12<br>West Bay, Doha 20451</span></div>
    <div class="contact-row"><svg width="14" height="14" viewBox="0 0 14 14"><path d="M3 0 L5.5 3.5 L4 5.5 C5 7.5 6.5 9 8.5 10 L10.5 8.5 L14 11 L12 14 C5.5 13.5 .5 8.5 0 2 Z" fill="#fff"/></svg><span>(555) 014-3300</span></div>
    <div class="contact-row"><svg width="14" height="11" viewBox="0 0 14 11"><rect width="14" height="11" fill="#fff"/><path d="M0 0 L7 6 L14 0" fill="none" stroke="#9b9b9b" stroke-width="1.2"/></svg><span>info@mptr-example.com</span></div>
  </div>
  <div class="footer-col footer-follow">
    <h4>Follow Us</h4>
    <div class="social"><span></span><span></span><span></span><span></span></div>
  </div>
  <div class="footer-bottom">© 2017 Company Name&nbsp; All right reserved</div>
</footer>

</body>
</html>
```